Valdane Companies Business Card Design

We need a new business card for our Private Equity Real Estate Development firm, “Valdane” and our EB-5 regional center “Thornmere Regional Center” on one card. We prefer a design that is simple, elegant, and represents the luxury products we design and build as well as the financial security and stability our successful history has produced. We are an industry leader in our field and 3rd generation family business that has evolved into an institutional quality investment platform. Considered design size is standard business card dimensions (3.5 x 2 inches with an additional 1/8 inch space for design elements or backgrounds that extend beyond the finished size of your piece.

Target Market(s)

• High net worth individuals
• Highly skilled technical workers and physicians in the US seeking investment-based immigration opportunities
• Sophisticated private equity investors
• Intermediary partners include domestic attorneys and investment brokers, as well as international agent networks
• US real estate developers

Industry/Entity Type

Finance

Contact Information for Business Card

(Providing placeholder info for personal information, please design for longer character spaces, longer names and addresses etc..)
• Logo for Valdane
• Logo for Thornmere Regional Center
• Full name: Marcus Valdane
• Job title: CEO
• Email address: mvaldane@valdanecompanies.com
• Cell phone number: +1.555.314.2287
• Office number +1.555.628.4410
• Office address: Larkfield Court 5, 4817 Vista Orilla, Ashcombe, OR.
• Website: www.valdanecompanies.com

Font styles to use
Serif
Sans Serif

Colors
ec1f27
ffffff
000000

Requirements
Must have
• • Logo for Valdane
• • Logo for Thornmere Regional Center
• - Use rounded corners
• (See .ai file included for logos)
Nice to have
• • Simple, elegant design
• • Aesthetically compatible with our website design (www.valdanecompanies.com)
• • Color palette including but not limited to white, black, and red (as per logos)
Should not have
• - Not too much red color
• - Do not stack both logos on top of each other

```html
<!DOCTYPE html>
<html lang="en">
<head>
<meta charset="utf-8">
<title>Valdane Companies Business Card</title>
<link rel="stylesheet" href="https://fonts.googleapis.com/css2?family=Cinzel:wght@400;600&family=Open+Sans:wght@400;600&display=swap">
<style>
  :root {
    --backdrop: #8c8c8c;
    --card-front: #2e2e2e;
    --card-back: #282828;
    --silver: #cfcfcf;
    --silver-dark: #9a9a9a;
    --white: #ffffff;
    --rule: #5a5a5a;
    --pattern-a: #2d2d2d;
    --pattern-b: #242424;
  }
  * { margin: 0; padding: 0; box-sizing: border-box; }
  html, body { width: 1200px; height: 1200px; overflow: hidden; }
  body { background: var(--backdrop); position: relative; font-family: "Open Sans", Arial, sans-serif; }

  .card {
    position: absolute;
    top: 310px;
    height: 595px;
    border-radius: 3px;
    box-shadow: 2px 3px 6px rgba(0,0,0,0.35);
    overflow: hidden;
  }
  .card--front { left: 234px; width: 364px; background: var(--card-front); text-align: center; color: var(--white); }
  .card--back { left: 628px; width: 367px; background: var(--card-back); }

  .brand-mark { position: absolute; left: 154px; top: 72px; width: 56px; height: 56px; background: var(--silver-dark); }
  .brand-name {
    position: absolute; left: 0; right: 0; top: 178px;
    font-family: "Cinzel", Georgia, serif; font-weight: 600;
    font-size: 29px; letter-spacing: 1px; color: var(--silver);
    white-space: nowrap;
  }

  .person { position: absolute; left: 0; right: 0; top: 344px; }
  .person__name { font-family: "Cinzel", Georgia, serif; font-weight: 400; font-size: 23px; letter-spacing: 0.5px; }
  .person__title { font-size: 14px; margin-top: 2px; }

  .divider { position: absolute; left: 69px; width: 226px; height: 1px; background: var(--rule); }
  .divider--upper { top: 402px; }
  .divider--lower { top: 508px; }

  .contact { position: absolute; left: 0; right: 0; top: 412px; font-size: 14.5px; line-height: 21.5px; }
  .contact b { font-weight: 600; }
  .address { position: absolute; left: 0; right: 0; top: 516px; font-size: 14.5px; line-height: 21.5px; }

  .pattern-field {
    position: absolute; inset: 0;
    background: linear-gradient(180deg, var(--pattern-a) 0%, var(--pattern-b) 100%);
  }
  .center-mark { position: absolute; left: 34px; top: 487px; width: 54px; height: 54px; background: var(--silver-dark); }
  .center-divider { position: absolute; left: 116px; top: 484px; width: 1px; height: 62px; background: var(--rule); }
  .center-name {
    position: absolute; left: 128px; top: 486px;
    font-family: "Cinzel", Georgia, serif; font-weight: 600;
    font-size: 21px; line-height: 27px; color: var(--silver);
    white-space: nowrap;
  }
</style>
</head>
<body>
  <section class="card card--front">
    <div class="brand-mark"></div>
    <div class="brand-name">Valdane Capital</div>
    <div class="person">
      <div class="person__name">MARCUS VALDANE</div>
      <div class="person__title">CEO</div>
    </div>
    <div class="divider divider--upper"></div>
    <div class="contact">
      <div><b>P:</b> +1.555.314.2287</div>
      <div><b>M:</b> +1.555.628.4410</div>
      <div><b>E:</b>&nbsp; mvaldane@valdanecompanies.com</div>
      <div><b>W:</b> www.valdanecompanies.com</div>
    </div>
    <div class="divider divider--lower"></div>
    <div class="address">
      <div>Larkfield Court 5, 4817 Vista</div>
      <div>Orilla, Ashcombe, OR</div>
    </div>
  </section>

  <section class="card card--back">
    <div class="pattern-field" role="img" aria-label="Faint repeated brand monogram pattern covering the card"></div>
    <div class="center-mark"></div>
    <div class="center-divider"></div>
    <div class="center-name">Thornmere<br>Regional Center</div>
  </section>
</body>
</html>
```